professional business card design for technology company

We are a small technology consulting firm, specialising in consulting based around Cloud and Managed services. Our colour scheme is yellow, blue and white, as you can see in the logos. Although we are based in melbourne australia, due to the nature of our work, our clients can be located anywhere. We are looking for a clean, professional, positive look - similar to our company logo

Target Market(s)

small business

Industry/Entity Type

Business

Contact Information for Business Card

eye catching, designed to incorporate some level of raised printing. Must contain website address, phone number, name and job title

Requirements
Must have
• Logo (attached) - use of the same colour scheme

```html
<!DOCTYPE html>
<html lang="en">
<head>
<meta charset="utf-8">
<title>Nubrio business card</title>
<link rel="stylesheet" href="https://fonts.googleapis.com/css2?family=Open+Sans:wght@400;700&display=swap">
<style>
  :root {
    --backdrop: #b9bec6;
    --card-white: #f2f2f2;
    --card-shade: #e2e2e2;
    --panel-grey: #5f6062;
    --stripe-grey: #c9c9c9;
    --brand-blue: #35a8e0;
    --brand-yellow: #f7d631;
    --ink-grey: #555659;
    --text-light: #ffffff;
  }
  * { box-sizing: border-box; margin: 0; padding: 0; }
  html, body {
    width: 1200px; height: 866px; overflow: hidden;
    background: var(--backdrop);
    font-family: "Open Sans", Arial, sans-serif;
  }
  .canvas { position: relative; width: 1200px; height: 866px; }

  .card {
    position: absolute;
    width: 560px; height: 320px;
    background: linear-gradient(135deg, var(--card-white) 0%, #fafafa 45%, var(--card-shade) 100%);
    box-shadow: 0 10px 28px rgba(0,0,0,0.22);
    overflow: hidden;
  }
  .card--front { left: 70px; top: 100px; }
  .card--back  { left: 570px; top: 460px; }

  .brand {
    display: flex; align-items: center; gap: 14px;
    color: var(--ink-grey); font-weight: 700; letter-spacing: -1px;
  }
  .brand__dot { border-radius: 50%; background: var(--brand-blue); flex: none; }

  .card--front .brand {
    position: absolute; left: 0; right: 0; top: 0; bottom: 0;
    justify-content: center; font-size: 84px;
  }
  .card--front .brand__dot { width: 46px; height: 46px; }

  .back__shape { position: absolute; inset: 0; }

  .card--back .brand {
    position: absolute; left: 40px; top: 180px; font-size: 52px; gap: 10px;
  }
  .card--back .brand__dot { width: 30px; height: 30px; }

  .contact {
    position: absolute; right: 30px; top: 26px;
    text-align: right; color: var(--text-light);
    font-size: 13px; line-height: 1.35;
  }
  .contact__name { font-weight: 700; font-size: 15px; }
  .contact__role { font-size: 14px; margin-bottom: 34px; }
  .contact__address { margin-bottom: 14px; }
  .contact__line { display: flex; justify-content: flex-end; align-items: center; gap: 6px; }
  .contact__line svg { width: 11px; height: 11px; fill: var(--text-light); }
  .contact__gap { height: 10px; }
</style>
</head>
<body>
<main class="canvas">

  <section class="card card--front" aria-label="Card front">
    <div class="brand"><span class="brand__dot"></span><span class="brand__name">Nubrio</span></div>
  </section>

  <section class="card card--back" aria-label="Card back">
    <svg class="back__shape" viewBox="0 0 560 320" preserveAspectRatio="none" aria-hidden="true">
      <path d="M215,0 C290,40 330,170 345,320 L560,320 L560,0 Z" fill="var(--stripe-grey)"/>
      <path d="M228,0 C305,45 340,170 352,320 L560,320 L560,0 Z" fill="var(--panel-grey)"/>
      <path d="M335,320 C338,230 330,150 300,90 C330,160 350,240 352,320 Z" fill="var(--brand-blue)"/>
    </svg>

    <div class="brand"><span class="brand__dot"></span><span class="brand__name">Nubrio</span></div>

    <div class="contact">
      <p class="contact__name">Maren Holt-Avery</p>
      <p class="contact__role">Consultant</p>
      <p class="contact__address">27 Level 9, Quay Tower<br>Harbour Street MEL</p>
      <p class="contact__line">013 468 2571
        <svg viewBox="0 0 24 24"><path d="M6.6 10.8a15 15 0 0 0 6.6 6.6l2.2-2.2c.3-.3.7-.4 1-.2 1.1.4 2.3.6 3.6.6.6 0 1 .4 1 1V20c0 .6-.4 1-1 1A17 17 0 0 1 3 4c0-.6.4-1 1-1h3.5c.6 0 1 .4 1 1 0 1.3.2 2.5.6 3.6.1.3 0 .7-.2 1z"/></svg></p>
      <p class="contact__line">013 468 2571
        <svg viewBox="0 0 24 24"><path d="M6 2h10v6H6zM3 9h18v11H3zM7 12h2v2H7zm4 0h2v2h-2zm4 0h2v2h-2zM7 16h10v2H7z"/></svg></p>
      <p class="contact__line">hello@nubrio.com
        <svg viewBox="0 0 24 24"><path d="M2 5h20v14H2zm2 2v.5l8 5 8-5V7l-8 5z"/></svg></p>
      <div class="contact__gap"></div>
      <p class="contact__line">www.nubrio-cloud.com</p>
    </div>
  </section>

</main>
</body>
</html>
```